Maple Grove Schools | brand new stationery!

We need stationery design with our new logo! Our company updated it's name and image and we like to incorporate the new one on our stationery, business cards and email signature. We are looking for fresh, new ideas!
Industry: Childcare, Elementary and Middle School
Company Name: Maple Grove Schools
Tagline: Bright Futures Start Here
Main colors: Blue, white and a little yellow
Star shape is something new for us! Do you see a way to incorporate it as a design element?

```html
<!DOCTYPE html>
<html lang="en">
<head>
<meta charset="utf-8">
<title>Maple Grove Schools – Stationery</title>
<link href="https://fonts.googleapis.com/css2?family=Lexend:wght@600&family=Open+Sans:wght@400;600;700&display=swap" rel="stylesheet">
<style>
  :root {
    --navy: #32366e;
    --yellow: #e8b522;
    --paper: #f4f4f4;
    --ink: #2b2b2b;
    --body-ink: #444;
    --backdrop: #e9e9e9;
  }
  * { box-sizing: border-box; margin: 0; padding: 0; }
  html, body { width: 1200px; height: 795px; overflow: hidden; background: var(--backdrop); }
  .stage { position: relative; width: 1200px; height: 795px; font-family: "Open Sans", sans-serif; color: var(--body-ink); }

  .sheet { position: absolute; background: var(--paper); overflow: hidden; box-shadow: 0 1px 3px rgba(0,0,0,.12); }
  .wave { position: absolute; left: 0; bottom: 0; width: 100%; }
  .wave .band { fill: var(--navy); }
  .wave .swoosh { fill: var(--yellow); }
  .tagline { position: absolute; left: 0; width: 100%; text-align: center; color: var(--yellow); font-weight: 700; letter-spacing: .06em; }

  .brand { font-family: "Lexend", sans-serif; font-weight: 600; color: var(--ink); line-height: 1.05; text-align: center; }
  .brand-dot { display: block; border-radius: 50%; background: var(--navy); margin: 0 auto; }

  /* Letterhead */
  .letterhead { left: 292px; top: 99px; width: 293px; height: 415px; }
  .letterhead .brand-block { position: absolute; left: 26px; top: 24px; width: 66px; }
  .letterhead .brand-dot { width: 18px; height: 18px; margin-bottom: 4px; }
  .letterhead .brand { font-size: 10px; }
  .letterhead .sender { position: absolute; left: 202px; top: 25px; font-size: 5.2px; line-height: 1.3; color: var(--body-ink); }
  .letterhead .sender .gap { margin-top: 2px; }
  .letterhead .letter-body { position: absolute; left: 28px; top: 127px; width: 241px; font-size: 5.2px; line-height: 8px; text-align: justify; }
  .letterhead .letter-body p { margin-bottom: 8px; }
  .letterhead .tagline { bottom: 9px; font-size: 5.6px; }

  /* Folder */
  .folder { left: 636px; top: 80px; width: 346px; height: 437px; }
  .folder .spine { position: absolute; top: 0; bottom: 0; width: 1px; background: #d6d6d6; }
  .folder .brand-block { position: absolute; left: 0; top: 130px; width: 100%; }
  .folder .brand-dot { width: 56px; height: 56px; margin-bottom: 18px; }
  .folder .brand { font-size: 33px; }
  .folder .tagline { bottom: 20px; font-size: 9px; }

  /* Business cards */
  .card { left: 187px; width: 132px; height: 75px; }
  .card-front { top: 550px; }
  .card-front .person { position: absolute; left: 9px; top: 11px; }
  .card-front .person .name { font-size: 4.8px; font-weight: 700; color: var(--navy); }
  .card-front .person .role { font-size: 3.8px; color: var(--yellow); }
  .card-front .brand-block { position: absolute; right: 8px; top: 7px; width: 50px; }
  .card-front .brand-dot { width: 12px; height: 12px; margin-bottom: 2px; }
  .card-front .brand { font-size: 7px; }
  .card-front .mini-tag { font-size: 2.4px; font-weight: 700; color: var(--navy); text-align: center; letter-spacing: .05em; margin-top: 1px; }
  .card-front .contact { position: absolute; bottom: 6px; font-size: 3.4px; line-height: 1.5; color: #fff; }
  .card-front .contact.left { left: 9px; }
  .card-front .contact.right { right: 8px; text-align: right; }
  .card-front .icon { display: inline-block; width: 3px; height: 3px; border-radius: 50%; background: var(--yellow); margin-right: 1.5px; vertical-align: middle; }
  .card-back { top: 646px; background: var(--navy); }
  .card-back .pattern { position: absolute; inset: 0; background: linear-gradient(135deg, #4a4e85, var(--navy) 60%); }

  /* Envelope front */
  .envelope-front { left: 353px; top: 561px; width: 328px; height: 157px; }
  .envelope-front .brand-block { position: absolute; left: 18px; top: 20px; width: 68px; }
  .envelope-front .brand-dot { width: 18px; height: 18px; margin-bottom: 4px; }
  .envelope-front .brand { font-size: 10px; }
  .envelope-front .return-address { margin-top: 3px; font-size: 5.2px; line-height: 1.3; color: var(--body-ink); text-align: left; }
  .envelope-front .tagline { bottom: 10px; font-size: 6.2px; }

  /* Envelope back */
  .envelope-back { left: 713px; top: 561px; width: 329px; height: 157px; }
  .envelope-back .flap { position: absolute; left: 0; top: 0; width: 100%; height: 58px; }
  .envelope-back .flap path { fill: var(--navy); }
  .envelope-back .flap-name { position: absolute; left: 0; top: 20px; width: 100%; text-align: center; font-family: "Lexend", sans-serif; font-weight: 600; font-size: 10px; color: #fff; }
</style>
</head>
<body>
<div class="stage">

  <!-- Letterhead -->
  <section class="sheet letterhead">
    <div class="brand-block">
      <span class="brand-dot"></span>
      <div class="brand">Maple Grove<br>Schools</div>
    </div>
    <address class="sender" style="font-style:normal">
      Maple Grove Schools<br>48 Orchard Lane, Suite 3<br>Linfield, MA 01900
      <div class="gap">&#9742; (555) 310-4482<br>&#9993; hello@maplegrove.org<br>&#9675; www.maplegrove.org</div>
    </address>
    <div class="letter-body">
      <p>Dear customer,</p>
      <p>Lorem ipsum dolor sit amet, consectetur adipisicing elit, sed do eiusmod tempor incididunt ut labore et dolore magna aliqua. Ut enim ad minim veniam, quis nostrud exercitation ullamco laboris nisi ut aliquip ex ea commodo consequat. Duis aute irure dolor in reprehenderit in voluptate velit esse cillum dolore eu fugiat nulla pariatur. Excepteur sint occaecat cupidatat non proident, sunt in culpa qui officia deserunt mollit anim id est laborum.</p>
      <p>Lorem ipsum dolor sit amet, consectetur adipisicing elit, sed do eiusmod tempor incididunt ut labore et dolore magna aliqua. Ut enim ad minim veniam, quis nostrud exercitation ullamco laboris nisi ut aliquip ex ea commodo consequat. Duis aute irure dolor in reprehenderit in voluptate velit esse cillum dolore eu fugiat nulla pariatur. Excepteur sint occaecat cupidatat non proident, sunt in culpa qui officia deserunt mollit anim id est laborum.</p>
      <p>Lorem ipsum dolor sit amet, consectetur adipisicing elit, sed do eiusmod tempor incididunt ut labore et dolore magna aliqua. Ut enim ad minim veniam, quis nostrud exercitation ullamco laboris nisi ut aliquip ex ea commodo consequat. Duis aute irure dolor in reprehenderit in voluptate velit esse cillum dolore eu fugiat nulla pariatur. Excepteur sint occaecat cupidatat non proident, sunt in culpa qui officia deserunt mollit anim id est laborum.</p>
    </div>
    <svg class="wave" viewBox="0 0 293 63" height="63" preserveAspectRatio="none">
      <path class="band" d="M0,0 C80,32 150,42 205,40 C245,38 272,33 293,28 L293,63 L0,63Z"/>
      <path class="swoosh" d="M110,34 C175,42 240,32 293,18 L293,22 C240,37 175,45 110,36Z"/>
    </svg>
    <div class="tagline">Bright Futures Start Here</div>
  </section>

  <!-- Presentation folder -->
  <section class="sheet folder">
    <span class="spine" style="left:5px"></span>
    <span class="spine" style="left:10px"></span>
    <span class="spine" style="left:19px"></span>
    <div class="brand-block">
      <span class="brand-dot"></span>
      <div class="brand">Maple Grove<br>Schools</div>
    </div>
    <svg class="wave" viewBox="0 0 346 94" height="94" preserveAspectRatio="none">
      <path class="band" d="M0,0 C90,38 170,52 240,50 C290,48 325,42 346,38 L346,94 L0,94Z"/>
      <path class="swoosh" d="M100,32 C180,50 270,42 346,25 L346,33 C270,50 180,56 100,35Z"/>
    </svg>
    <div class="tagline">Bright Futures Start Here</div>
  </section>

  <!-- Business card front -->
  <section class="sheet card card-front">
    <div class="person">
      <div class="name">DANA R. WHITFIELD</div>
      <div class="role">Founder &amp; CEO</div>
    </div>
    <div class="brand-block">
      <span class="brand-dot"></span>
      <div class="brand">Maple Grove<br>Schools</div>
      <div class="mini-tag">Bright Futures Start Here</div>
    </div>
    <svg class="wave" viewBox="0 0 132 52" height="52" preserveAspectRatio="none">
      <path class="band" d="M0,0 C25,20 50,30 80,30 C105,30 120,27 132,24 L132,52 L0,52Z"/>
      <path class="swoosh" d="M20,16 C55,34 100,32 132,22 L132,25 C100,35 55,37 20,18Z"/>
    </svg>
    <div class="contact left">
      <div><span class="icon"></span>(555) 310-4482</div>
      <div><span class="icon"></span>hello@maplegrove.org</div>
      <div><span class="icon"></span>www.maplegrove.org</div>
    </div>
    <div class="contact right">48 Orchard Lane, Suite 3<br>Linfield, MA 01900</div>
  </section>

  <!-- Business card back -->
  <section class="sheet card card-back">
    <div class="pattern" role="img" aria-label="Repeating brand pattern on navy"></div>
  </section>

  <!-- Envelope front -->
  <section class="sheet envelope-front">
    <div class="brand-block">
      <span class="brand-dot"></span>
      <div class="brand">Maple Grove<br>Schools</div>
      <div class="return-address">77 Birch Road Suite<br>5 Fairview, MS 38700</div>
    </div>
    <svg class="wave" viewBox="0 0 328 70" height="70" preserveAspectRatio="none">
      <path class="band" d="M0,0 C70,32 150,42 220,40 C270,38 305,32 328,26 L328,70 L0,70Z"/>
      <path class="swoosh" d="M125,36 C200,42 270,34 328,20 L328,25 C270,38 200,46 125,38Z"/>
    </svg>
    <div class="tagline">Bright Futures Start Here</div>
  </section>

  <!-- Envelope back -->
  <section class="sheet envelope-back">
    <svg class="flap" viewBox="0 0 329 58" preserveAspectRatio="none">
      <path d="M0,0 L329,0 L323,50 Q322,56 315,56 L14,56 Q7,56 6,50 Z"/>
    </svg>
    <div class="flap-name">Maple Grove Schools</div>
  </section>

</div>
</body>
</html>
```